TalkHarbor - Language Coaching Services

Sleek, innovative, trendy design for Language Coaching business.

TalkHarbor is a new UK based company that provides Language Coaching services. We offer highly personalized on-line and face to face language courses. We also impart learning techniques workshops based on the latest neuroscience research for second-language acquisition.

Target Market(s)

See attached info

Industry/Entity Type

Consulting

Contact Information for Business Card

TalkHarbor
DaniaKV@talkharbor.co.uk
TalkHarbor.co.uk
London, UK

Font styles to use
Sans Serif

```html
<!DOCTYPE html>
<html lang="en">
<head>
<meta charset="utf-8">
<title>TalkHarbor – Business Card</title>
<link rel="stylesheet" href="https://fonts.googleapis.com/css2?family=Ubuntu:wght@300;400;500;700&display=swap">
<style>
  :root {
    --backdrop: #3a3a3c;
    --card: #2b2829;
    --card-edge: #353233;
    --accent: #1fa6d9;
    --accent-deep: #1487b8;
    --ink-light: #f2f2f2;
  }
  * { box-sizing: border-box; margin: 0; padding: 0; }
  html, body {
    width: 1200px; height: 900px; overflow: hidden;
    background: var(--backdrop);
    font-family: "Ubuntu", sans-serif;
  }
  .stage {
    width: 1200px; height: 900px;
    display: flex; justify-content: center; align-items: center; gap: 80px;
  }
  .card {
    width: 380px; height: 680px;
    background: linear-gradient(160deg, var(--card-edge), var(--card));
    border-radius: 4px;
    box-shadow: 0 18px 40px rgba(0,0,0,.45);
    position: relative;
    color: var(--ink-light);
  }
  /* Front */
  .card-front .brand-top {
    position: absolute; top: 48px; left: 42px;
    font-size: 34px; font-weight: 500; color: var(--accent);
    letter-spacing: 1px;
  }
  .card-front .brand-mark {
    position: absolute; top: 120px; left: 50%;
    width: 280px; height: 280px; margin-left: -140px;
    border: 16px solid var(--accent); border-radius: 50%;
  }
  .card-front .details {
    position: absolute; top: 428px; left: 0; right: 0;
    text-align: center;
  }
  .details .company {
    font-size: 26px; font-weight: 700; color: var(--accent);
    margin-bottom: 14px;
  }
  .details .icons {
    display: flex; justify-content: center; gap: 14px; margin-bottom: 14px;
  }
  .details .icons svg { width: 20px; height: 20px; fill: var(--accent); }
  .details .line {
    font-size: 17px; line-height: 27px; color: var(--ink-light);
  }
  .details .address {
    font-size: 17px; line-height: 27px; color: var(--accent);
  }
  .card-front .rule {
    position: absolute; bottom: 40px; left: 30px; right: 30px;
    height: 1px; background: var(--accent-deep);
  }
  /* Back */
  .card-back .back-lockup {
    position: absolute; top: 210px; left: 0; right: 0;
    display: flex; flex-direction: column; align-items: center;
  }
  .back-lockup .brand-mark {
    width: 120px; height: 120px;
    border: 8px solid var(--accent); border-radius: 50%;
    margin-bottom: 22px;
  }
  .back-lockup .brand-name {
    font-size: 40px; font-weight: 500; color: var(--accent);
    letter-spacing: 1px;
  }
  .back-lockup .web {
    margin-top: 8px; font-size: 17px; color: var(--ink-light);
  }
</style>
</head>
<body>
<main class="stage">
  <section class="card card-front">
    <div class="brand-top">TalkHarbor</div>
    <div class="brand-mark"></div>
    <div class="details">
      <div class="company">TalkHarbor</div>
      <div class="icons">
        <svg viewBox="0 0 24 24" aria-label="phone"><path d="M6.6 10.8a15 15 0 0 0 6.6 6.6l2.2-2.2a1 1 0 0 1 1-.25 11.4 11.4 0 0 0 3.6.57 1 1 0 0 1 1 1V20a1 1 0 0 1-1 1A17 17 0 0 1 3 4a1 1 0 0 1 1-1h3.5a1 1 0 0 1 1 1c0 1.25.2 2.45.57 3.57a1 1 0 0 1-.25 1z"/></svg>
        <svg viewBox="0 0 24 24" aria-label="email"><path d="M2 5h20v14H2z M2 5l10 8 10-8" stroke="#2b2829" stroke-width="1.5"/></svg>
        <svg viewBox="0 0 24 24" aria-label="website"><circle cx="12" cy="12" r="10"/><path d="M2 12h20M12 2c3 3 3 17 0 20M12 2c-3 3-3 17 0 20M4 7h16M4 17h16" stroke="#2b2829" stroke-width="1.3" fill="none"/></svg>
        <svg viewBox="0 0 24 24" aria-label="location"><path d="M12 2a7 7 0 0 0-7 7c0 5 7 13 7 13s7-8 7-13a7 7 0 0 0-7-7zm0 9.5A2.5 2.5 0 1 1 12 6.5a2.5 2.5 0 0 1 0 5z"/></svg>
      </div>
      <div class="line">+44 1632 960718</div>
      <div class="line">DaniaKV@talkharbor.co.uk</div>
      <div class="line">www.TalkHarbor.co.uk</div>
      <div class="address">12 Harbour Lane, TN34 1QA,<br>London, UK</div>
    </div>
    <div class="rule"></div>
  </section>

  <section class="card card-back">
    <div class="back-lockup">
      <div class="brand-mark"></div>
      <div class="brand-name">TalkHarbor</div>
      <div class="web">www.talkharbor.co.uk</div>
    </div>
  </section>
</main>
</body>
</html>
```